Heron Loan Partners Business Card

We need a business card design for our mortgage servicing company. In addition to servicing the loans of homeowners, we help homeowners with purchasing their homes and any mortgage refinancing. We would like to see designs that use the colors in the logo attached below (gold-ish yellow and navy blue), and any other design you deem fit! The design should communicate a simpler life with smart mortgages provided by Heron.

```html
<!DOCTYPE html>
<html lang="en">
<head>
<meta charset="utf-8">
<title>Heron Loan Partners – Business Card</title>
<link href="https://fonts.googleapis.com/css2?family=Open+Sans:wght@400;600;700&display=swap" rel="stylesheet">
<style>
  :root {
    --stage: #2f2f2f;
    --gold: #deb03b;
    --gold-deep: #c99a2a;
    --navy: #231c57;
    --ink: #141414;
    --paper: #ffffff;
  }
  * { box-sizing: border-box; margin: 0; padding: 0; }
  html, body { width: 1200px; height: 780px; overflow: hidden; }
  body {
    background: var(--stage);
    font-family: "Open Sans", sans-serif;
    position: relative;
  }
  .card {
    position: absolute;
    top: 235px;
    width: 540px;
    height: 309px;
    overflow: hidden;
  }
  /* Back side */
  .card-back { left: 40px; background: var(--gold); }
  .back-pattern {
    position: absolute; inset: 0;
    background: linear-gradient(135deg, #e3b744 0%, var(--gold) 50%, var(--gold-deep) 100%);
  }
  .back-mark {
    position: absolute;
    right: 70px; top: 140px;
    font-weight: 700;
    font-size: 15px;
    color: var(--paper);
    letter-spacing: 0.02em;
  }
  /* Front side */
  .card-front { left: 620px; background: var(--paper); }
  .front-mark {
    position: absolute;
    right: 34px; top: 40px;
    font-weight: 700;
    font-size: 26px;
    color: var(--navy);
    display: flex; align-items: center; gap: 10px;
  }
  .front-mark .dot {
    width: 14px; height: 14px; border-radius: 50%;
    background: var(--gold);
  }
  .accent-bar {
    position: absolute;
    left: 0; top: 142px;
    width: 16px; height: 48px;
    background: var(--gold);
  }
  .identity { position: absolute; left: 30px; top: 138px; }
  .person-name {
    font-weight: 700; font-size: 30px; line-height: 1.05;
    letter-spacing: 0.02em;
  }
  .person-name .given { color: var(--gold); }
  .person-name .family { color: var(--navy); }
  .person-role {
    font-weight: 600; font-size: 15px; color: var(--ink);
    letter-spacing: 0.03em; margin-top: 2px;
  }
  .address {
    position: absolute; left: 30px; top: 212px;
    font-size: 14px; line-height: 1.3; color: var(--ink); letter-spacing: 0.03em;
  }
  .contacts {
    position: absolute; left: 30px; top: 252px;
    list-style: none;
  }
  .contacts li {
    display: flex; align-items: center; gap: 8px;
    font-size: 13px; line-height: 17px; color: var(--ink); letter-spacing: 0.03em;
  }
  .contacts svg { width: 12px; height: 12px; flex: none; }
</style>
</head>
<body>
  <section class="card card-back" aria-label="Card back">
    <div class="back-pattern" role="img" aria-label="Repeating tonal brand pattern on gold"></div>
    <span class="back-mark">Heron Loan Partners</span>
  </section>

  <section class="card card-front" aria-label="Card front">
    <div class="front-mark"><span class="dot"></span>Heron Loan Partners</div>
    <div class="accent-bar"></div>
    <div class="identity">
      <h1 class="person-name"><span class="given">Livia</span> <span class="family">Marchetti</span></h1>
      <p class="person-role">Managing Director</p>
    </div>
    <p class="address">1840 Lakeshore Ave. Suite 310<br>Denton, TX 76201</p>
    <ul class="contacts">
      <li>
        <svg viewBox="0 0 24 24" aria-hidden="true"><path fill="#deb03b" d="M6.6 10.8a15.1 15.1 0 0 0 6.6 6.6l2.2-2.2c.3-.3.7-.4 1-.2 1.1.4 2.3.6 3.6.6.6 0 1 .4 1 1V20c0 .6-.4 1-1 1A17 17 0 0 1 3 4c0-.6.4-1 1-1h3.5c.6 0 1 .4 1 1 0 1.3.2 2.5.6 3.6.1.3 0 .7-.2 1z"/></svg>
        (940) 555-0147
      </li>
      <li>
        <svg viewBox="0 0 24 24" aria-hidden="true"><rect x="2" y="5" width="20" height="14" rx="2" fill="#deb03b"/><path d="M3 6l9 7 9-7" fill="none" stroke="#fff" stroke-width="1.6"/></svg>
        info@website.com
      </li>
      <li>
        <svg viewBox="0 0 24 24" aria-hidden="true"><circle cx="12" cy="12" r="10" fill="#deb03b"/><path d="M2 12h20M12 2c3 3 3 17 0 20M12 2c-3 3-3 17 0 20" fill="none" stroke="#fff" stroke-width="1.4"/></svg>
        www.website.com
      </li>
    </ul>
  </section>
</body>
</html>
```